you will use Ai to Copy the website Brivanta.com to come up with the basic frame work and it will give you the understanding of how I would like Kelbrava.com to be like. Kelbrava.com is a peer to peer rv rental site very similar to both of the other rv rental sites the difference is that are commission based 20% and above per rental and we will be one flat monthly rate and they keep all the earnings. Below is photo that will help you with the color scheme and the look and feel of the design

1 page

```html
<!DOCTYPE html>
<html lang="en">
<head>
<meta charset="utf-8">
<title>Kelbrava – Keep 100% of Your RV Rental Income</title>
<link href="https://fonts.googleapis.com/css2?family=Poppins:wght@400;500;600;700&display=swap" rel="stylesheet">
<style>
:root{
  --green:#6ba32c;
  --navy:#0b1425;
  --cream:#f8f7ec;
  --ink:#2b2b2b;
  --muted:#4a4a4a;
  --white:#ffffff;
  --border:#cfcfc4;
}
*{margin:0;padding:0;box-sizing:border-box}
html,body{width:1200px;height:4515px;overflow:hidden}
body{font-family:'Poppins',sans-serif;background:var(--cream);color:var(--ink);position:relative}
.abs{position:absolute}

/* Header / hero */
.hero{position:absolute;left:0;top:0;width:1200px;height:640px}
.hero-photo{position:absolute;left:0;top:0;width:1200px;height:640px;background:linear-gradient(180deg,#1a2e24 0%,#45574a 100%)}
.hero-wave{position:absolute;left:0;top:0;width:1200px;height:640px}
.brand{left:56px;top:46px;font-size:28px;font-weight:700;color:var(--white)}
.nav{left:250px;top:54px;display:flex;gap:32px;font-size:15px;color:var(--white)}
.btn-login{left:880px;top:39px;width:118px;height:49px;background:var(--green);color:var(--white);border-radius:6px;font-size:15px;display:flex;align-items:center;justify-content:center}
.btn-signup{left:1025px;top:39px;width:118px;height:49px;border:1.5px solid var(--white);color:var(--white);border-radius:6px;font-size:15px;display:flex;align-items:center;justify-content:center}
.hero-title{left:112px;top:182px;font-size:37px;font-weight:700;color:var(--white)}
.hero-title span{color:var(--green)}
.hero-text{left:112px;top:256px;width:660px;font-size:15px;line-height:29px;color:var(--white)}
.search{left:112px;top:383px;width:338px;height:49px;background:var(--white);border-radius:4px;display:flex;align-items:center;gap:8px;padding-left:16px;font-size:14px;color:#333}
.btn-search{left:470px;top:383px;width:150px;height:49px;background:var(--green);color:var(--white);border-radius:4px;font-size:15px;display:flex;align-items:center;justify-content:center}

/* Why */
.h2{font-size:37px;font-weight:700;color:var(--ink)}
.rule{height:4px;width:180px;background:var(--green)}
.why-text{left:503px;top:726px;width:590px;font-size:15px;line-height:30px;color:var(--muted)}
.why-card{width:224px;height:276px;border:1.5px solid var(--border);border-radius:12px;top:914px;text-align:center;padding:26px 14px 0}
.why-card svg{display:block;margin:0 auto 12px}
.why-card h3{font-size:15px;font-weight:600;line-height:23px;margin-bottom:14px}
.why-card p{font-size:12.5px;line-height:21.5px;color:var(--muted)}

/* Popular */
.center{left:0;width:1200px;text-align:center}
.lead{font-size:15.5px;line-height:30px;color:var(--muted)}
.rv-card{top:1517px;width:314px;height:415px;background:var(--white);border-radius:14px;overflow:hidden;box-shadow:0 4px 14px rgba(0,0,0,.08)}
.rv-photo{height:252px}
.rv-body{padding:24px 26px 0}
.rv-body h3{font-size:17.5px;font-weight:600;margin-bottom:8px}
.rv-body .from{font-size:14px;color:var(--muted)}
.rv-meta{display:flex;justify-content:space-between;align-items:center;margin-top:30px;font-size:15px}
.rv-meta .rate{display:flex;align-items:center;gap:6px;color:var(--muted)}
.rv-meta .price b{font-size:18px;font-weight:600;color:var(--ink)}
.rv-meta .price{color:var(--muted)}

/* Dark about */
.about{left:0;top:2030px;width:1200px;height:712px}
.about-title{left:112px;top:2186px;font-size:37px;font-weight:700;color:var(--white)}
.about-text{left:110px;top:2286px;width:500px;font-size:15px;line-height:30.5px;color:#e6e6e6}
.about-photo{left:636px;top:2183px;width:454px;height:433px;border-radius:16px;background:linear-gradient(180deg,#4a4f6a 0%,#3a3030 100%)}

/* Top-rated */
.btn-view{left:515px;top:3080px;width:167px;height:49px;background:var(--green);color:var(--white);border-radius:5px;font-size:15px;display:flex;align-items:center;justify-content:center}
.dest{border:2px solid var(--green);border-radius:18px}

/* Footer */
.footer-col{top:3988px}
.footer-col h4{font-size:18px;font-weight:700;color:var(--white);margin-bottom:20px}
.footer-col li{list-style:none;font-size:15px;color:var(--white);height:42.6px}
.copy{left:0;top:4476px;width:1200px;height:39px;background:var(--green);color:var(--white);font-size:13px;display:flex;align-items:center;justify-content:center}
</style>
</head>
<body>

<header class="hero">
  <div class="hero-photo" role="img" aria-label="Photo of a camper van parked on a lakeside cliff at dusk with two travellers looking over the water"></div>
  <svg class="hero-wave" viewBox="0 0 1200 640" aria-hidden="true">
    <path d="M0 600 C120 640 220 600 320 580 C420 560 520 600 640 610 C780 620 900 590 1000 560 C1080 540 1150 570 1200 590 L1200 640 L0 640 Z" fill="var(--cream)"/>
  </svg>
  <div class="abs brand">Kelbrava</div>
  <nav class="abs nav"><span>Find an RV</span><span>List Your RV</span><span>How It Works</span><span>Subscription</span><span>Destinations</span></nav>
  <div class="abs btn-login">Log In</div>
  <div class="abs btn-signup">Sign Up</div>
  <h1 class="abs hero-title">Keep 100% of Your RV <span>Rental Income</span></h1>
  <p class="abs hero-text">Kelbrava is the subscription-based RV rental marketplace where owners pay one affordable monthly fee instead of high commissions. List your RV, connect with verified renters, and keep every dollar you earn.</p>
  <div class="abs search">
    <svg width="14" height="18" viewBox="0 0 14 18"><path d="M7 0a7 7 0 0 0-7 7c0 5 7 11 7 11s7-6 7-11a7 7 0 0 0-7-7zm0 10a3 3 0 1 1 0-6 3 3 0 0 1 0 6z" fill="#111"/></svg>
    Where do you want to go?
  </div>
  <div class="abs btn-search">Search RVs</div>
</header>

<section>
  <h2 class="abs h2" style="left:112px;top:722px">Why Kelbrava?</h2>
  <div class="abs rule" style="left:112px;top:788px"></div>
  <p class="abs why-text">More Freedom. More Earnings. More Adventures.<br>Unlike commission-based rental platforms, Kelbrava lets owners pay one affordable monthly subscription and keep 100% of every booking. More income for owners means better value for everyone.</p>

  <div class="abs why-card" style="left:112px">
    <svg width="46" height="46" viewBox="0 0 46 46"><circle cx="23" cy="23" r="20" fill="none" stroke="var(--green)" stroke-width="2.5"/><circle cx="23" cy="18" r="5" fill="var(--green)"/><path d="M13 33c2-6 18-6 20 0" fill="var(--green)"/></svg>
    <h3>Thousands of<br>Unique RVs</h3>
    <p>Browse a diverse selection of motorhomes, camper vans, travel trailers, and luxury RVs from trusted owners across the country.</p>
  </div>
  <div class="abs why-card" style="left:363px">
    <svg width="46" height="46" viewBox="0 0 46 46"><circle cx="23" cy="23" r="13" fill="none" stroke="var(--green)" stroke-width="2.5"/><path d="M23 15l2.5 5 5.5.8-4 3.9 1 5.4-5-2.6-5 2.6 1-5.4-4-3.9 5.5-.8z" fill="var(--green)"/><g stroke="var(--green)" stroke-width="2"><path d="M23 2v5M23 39v5M2 23h5M39 23h5M8 8l4 4M34 34l4 4M38 8l-4 4M8 38l4-4"/></g></svg>
    <h3>Keep 100% of Your<br>Earnings</h3>
    <p>Unlike platforms that charge high commission fees, Kelbrava owners pay one affordable monthly fee.</p>
  </div>
  <div class="abs why-card" style="left:613px">
    <svg width="46" height="46" viewBox="0 0 46 46"><rect x="8" y="16" width="30" height="18" rx="4" fill="none" stroke="var(--green)" stroke-width="2.5"/><path d="M12 16l3-7h16l3 7" fill="none" stroke="var(--green)" stroke-width="2.5"/><circle cx="15" cy="26" r="2.5" fill="var(--green)"/><circle cx="31" cy="26" r="2.5" fill="var(--green)"/><rect x="10" y="34" width="5" height="5" fill="var(--green)"/><rect x="31" y="34" width="5" height="5" fill="var(--green)"/></svg>
    <h3>Verified Owners &amp;<br>Renters</h3>
    <p>Every account is verified to build a trusted marketplace where owners and travelers book with confidence.</p>
  </div>
  <div class="abs why-card" style="left:865px">
    <svg width="46" height="46" viewBox="0 0 46 46"><circle cx="23" cy="23" r="19" fill="none" stroke="var(--green)" stroke-width="2.5"/><circle cx="23" cy="23" r="13" fill="var(--green)"/><path d="M17 23l4 4 8-8" fill="none" stroke="#fff" stroke-width="2.5"/></svg>
    <h3>Nationwide<br>Availability</h3>
    <p>Whether you're exploring national parks, coastal highways, or cities, find RV rentals across the country.</p>
  </div>
</section>

<section>
  <h2 class="abs h2 center" style="top:1295px">Popular RV Rentals</h2>
  <p class="abs lead" style="left:140px;top:1407px;width:920px;text-align:center">Discover some of the most sought-after RVs on Kelbrava. From luxury motorhomes to cozy camper vans, find the perfect ride for your next unforgettable adventure.</p>

  <article class="abs rv-card" style="left:112px">
    <div class="rv-photo" role="img" aria-label="Photo of a silver camper van parked among pine trees" style="background:linear-gradient(180deg,#55603f,#6e6a58)"></div>
    <div class="rv-body"><h3>Luxury on Wheels</h3><p class="from">Starting at $299/night</p>
      <div class="rv-meta"><span class="rate"><svg width="20" height="20" viewBox="0 0 20 20"><path d="M10 1l2.7 5.6 6.1.9-4.4 4.3 1 6.1L10 15l-5.4 2.9 1-6.1L1.2 7.5l6.1-.9z" fill="#f4b400"/></svg>5.0(22)</span><span class="price"><b>$189</b> /night</span></div></div>
  </article>
  <article class="abs rv-card" style="left:445px">
    <div class="rv-photo" role="img" aria-label="Photo of a white passenger van in front of a brick wall" style="background:linear-gradient(180deg,#8e5240,#a88a7e)"></div>
    <div class="rv-body"><h3>Adventure Made Simple</h3><p class="from">Starting at $129/night</p>
      <div class="rv-meta"><span class="rate"><svg width="20" height="20" viewBox="0 0 20 20"><path d="M10 1l2.7 5.6 6.1.9-4.4 4.3 1 6.1L10 15l-5.4 2.9 1-6.1L1.2 7.5l6.1-.9z" fill="#f4b400"/></svg>5.0(22)</span><span class="price"><b>$129</b> /night</span></div></div>
  </article>
  <article class="abs rv-card" style="left:778px">
    <div class="rv-photo" role="img" aria-label="Photo of a white class C motorhome parked under a blue sky" style="background:linear-gradient(180deg,#5a7cb6,#9aa79a)"></div>
    <div class="rv-body"><h3>Bring the Comforts of Home</h3><p class="from">Starting at $99/night</p>
      <div class="rv-meta"><span class="rate"><svg width="20" height="20" viewBox="0 0 20 20"><path d="M10 1l2.7 5.6 6.1.9-4.4 4.3 1 6.1L10 15l-5.4 2.9 1-6.1L1.2 7.5l6.1-.9z" fill="#f4b400"/></svg>5.0(22)</span><span class="price"><b>$99</b> /night</span></div></div>
  </article>
</section>

<section>
  <svg class="abs about" viewBox="0 0 1200 712" preserveAspectRatio="none" aria-hidden="true">
    <path d="M0 50 C120 20 200 40 300 60 C420 80 520 -10 680 10 C800 25 860 60 960 60 C1060 60 1120 30 1200 35 L1200 712 L0 712 Z" fill="var(--navy)"/>
  </svg>
  <h2 class="abs about-title">Adventure Starts Here</h2>
  <div class="abs rule" style="left:112px;top:2262px"></div>
  <div class="abs about-text">
    <p>Kelbrava is a modern peer-to-peer RV rental marketplace built for both RV owners and travelers. We believe renting an RV should be simple, affordable, and rewarding. That's why we've created a platform where owners pay one flat monthly subscription instead of expensive commission fees, allowing them to keep 100% of their rental earnings.</p>
    <p style="margin-top:30px">Whether you're planning a weekend escape, a cross-country road trip Kelbrava provides a secure and easy-to-use platform that connects trusted owners with adventure seekers across the country.</p>
  </div>
  <div class="abs about-photo" role="img" aria-label="Photo of friends celebrating with music beside a decorated camper at night"></div>
</section>

<section>
  <h2 class="abs h2 center" style="top:2840px">Top-Rated RVs for Every Adventure</h2>
  <div class="abs rule" style="left:510px;top:2919px"></div>
  <p class="abs lead" style="left:130px;top:2956px;width:940px;text-align:center">Discover some of the most sought-after RVs on Kelbrava. From luxury motorhomes to cozy camper vans, find the perfect ride for your next unforgettable adventure. Browse our most popular RV rentals selected by travelers across the country. Compare features, prices, and amenities to find the perfect home on wheels.</p>
  <div class="abs btn-view">View All RVs</div>

  <h2 class="abs h2" style="left:112px;top:3270px">Adventure Starts Everywhere</h2>
  <div class="abs rule" style="left:112px;top:3336px"></div>
  <div class="abs dest" style="left:112px;top:3399px;width:415px;height:340px;background:linear-gradient(180deg,#a98478,#5a5d44)" role="img" aria-label="Photo of a river valley at sunset with a bison grazing"></div>
  <div class="abs dest" style="left:548px;top:3434px;width:375px;height:305px;background:linear-gradient(180deg,#7d93ac,#4a5646)" role="img" aria-label="Photo of a hiker sitting on a rock overlooking mountains"></div>
  <div class="abs dest" style="left:944px;top:3434px;width:280px;height:305px;background:linear-gradient(180deg,#4a6288,#9a6a3e)" role="img" aria-label="Photo of a steaming hot spring with orange mineral terraces"></div>
</section>

<footer>
  <svg class="abs" style="left:0;top:3860px;width:1200px;height:620px" viewBox="0 0 1200 620" preserveAspectRatio="none" aria-hidden="true">
    <path d="M0 60 C140 20 260 30 380 55 C520 80 640 20 780 45 C900 65 980 10 1080 25 C1140 35 1180 50 1200 55 L1200 620 L0 620 Z" fill="var(--navy)"/>
  </svg>
  <div class="abs footer-col" style="left:116px"><h4>EXPLORE</h4><ul><li>Find an RV</li><li>Popular Destinations</li><li>Luxury RVs</li><li>Family RVs</li><li>Pet-Friendly RVs</li><li>Last-Minute Rentals</li><li>RV Deals</li><li>Gift Cards</li></ul></div>
  <div class="abs footer-col" style="left:382px"><h4>FOR OWNERS</h4><ul><li>List Your RV</li><li>How It Works</li><li>Subscription Plans</li><li>Owner Dashboard</li><li>Earnings Calculator</li><li>Insurance &amp; Protection</li><li>Owner Resources</li><li>Success Stories</li></ul></div>
  <div class="abs footer-col" style="left:680px"><h4>COMPANY</h4><ul><li>About Us</li><li>Careers</li><li>Press</li><li>Blog</li><li>Testimonials</li><li>Affiliate Program</li><li>Partners</li><li>Contact Us</li></ul></div>
  <div class="abs footer-col" style="left:941px"><h4>SUPPORT</h4><ul><li>Help Center</li><li>FAQs</li><li>Trust &amp; Safety</li><li>Cancellation Policy</li><li>Terms of Service</li><li>Privacy Policy</li><li>Cookie Policy</li><li>Accessibility</li></ul></div>
  <div class="abs copy">© 2026 Kelbrava.com. All Rights Reserved.</div>
</footer>

</body>
</html>
```